Adult Literacy Program - flyer to attract volunteers and students

We want a flyer that is engaging, colorful, modern and will appeal to our primary audience of adults aged 40-60. We are trying to attract both prospective volunteers (typically age 50+, mostly women) and students (typically aged 40+).
The flyer should feature diverse people working together in pairs of two, reading or talking, with a workbook or some reading material in front of them.

Our organization trains tutors to work one-on-one with adults who are learning how to read. Most of our adult students are non-native speakers of English. Many are of Haitian or Hispanic origin, so we would like some people who represent that demographic.

The Flyer should represent reading, learning, literacy, knowledge, growth,
and opportunities.
Our students are learning to read so they can advance their job opportunities.

Target Market(s)

Adults aged 40-60, primarily women, retired, volunteers

Industry/Entity Type

Education

Font styles to use
Serif
Sans Serif

Colors

Designer to choose colors to be used in the design.

Requirements
Must have
• - UPDATE: Should be designed as a TRI-FOLD brochure on 8.5 x 11 inch paper that will be folded into thirds.
• - Images of diverse people, women and men, who look Hispanic, Haitian and other nationalities as well as Caucasian.
• - Our logo on the front cover
Nice to have
• The sample flyer is very boring and dry! We are open to different ways of presenting the text.

```html
<!DOCTYPE html>
<html lang="en">
<head>
<meta charset="utf-8">
<title>Reading Circle Partners – Tri-fold Brochure</title>
<link href="https://fonts.googleapis.com/css2?family=Marcellus&family=Open+Sans:ital,wght@0,600;0,700;1,400&display=swap" rel="stylesheet">
<style>
  :root {
    --navy: #1c2f5e;
    --ink: #111111;
    --teal: #3fbfd3;
    --teal-deep: #1f8fa3;
    --teal-dark: #0d4f5e;
    --paper: #ffffff;
    --paper-shade: #d9d9d9;
    --stage: #f2f2f2;
  }
  * { margin: 0; padding: 0; box-sizing: border-box; }
  html, body { width: 1200px; height: 1200px; overflow: hidden; background: var(--stage); }
  .canvas { position: relative; width: 1200px; height: 1200px; }
  .brochure {
    position: absolute; left: 0; top: 150px; width: 1200px; height: 900px;
    font-family: "Open Sans", Arial, sans-serif; color: var(--ink);
    box-shadow: 0 6px 20px rgba(0,0,0,.15); overflow: hidden;
  }
  .brochure-art { position: absolute; inset: 0; }
  .txt { position: absolute; white-space: nowrap; }
  .section-title { font-family: "Marcellus", Georgia, serif; font-size: 37px; letter-spacing: 2px; color: var(--ink); font-weight: 400; }
  .body { font-weight: 600; font-size: 16px; letter-spacing: .6px; line-height: 23px; }
  .list-italic { font-style: italic; font-weight: 400; font-size: 16px; letter-spacing: .5px; line-height: 23px; }
  .callout { font-weight: 700; font-size: 27px; letter-spacing: .8px; }
  .small { font-weight: 600; font-size: 14px; letter-spacing: .6px; }
  .phone { font-weight: 700; font-size: 22px; letter-spacing: .8px; line-height: 28px; }
  .email { letter-spacing: .3px; }
  .brand-name {
    position: absolute; font-family: "Open Sans", Arial, sans-serif; font-weight: 700;
    color: var(--navy); text-align: center; line-height: 1.15;
  }
</style>
</head>
<body>
<div class="canvas">
  <section class="brochure">
    <svg class="brochure-art" width="1200" height="900" viewBox="0 0 1200 900" xmlns="http://www.w3.org/2000/svg">
      <defs>
        <linearGradient id="paperFold" x1="0" x2="1">
          <stop offset="0" stop-color="var(--paper)"/>
          <stop offset=".55" stop-color="var(--paper)"/>
          <stop offset="1" stop-color="var(--paper-shade)"/>
        </linearGradient>
        <linearGradient id="tealPanel" x1="0" x2="1">
          <stop offset="0" stop-color="#45c6d8"/>
          <stop offset=".7" stop-color="#3bbcd0"/>
          <stop offset="1" stop-color="#2aa3b7"/>
        </linearGradient>
        <linearGradient id="photoWarm" x1="0" y1="0" x2="1" y2="1">
          <stop offset="0" stop-color="#c9a98f"/>
          <stop offset=".5" stop-color="#a87c70"/>
          <stop offset="1" stop-color="#e07d8e"/>
        </linearGradient>
        <linearGradient id="photoLibrary" x1="0" y1="0" x2="1" y2="1">
          <stop offset="0" stop-color="#8a3a3e"/>
          <stop offset=".5" stop-color="#6d7a9a"/>
          <stop offset="1" stop-color="#4a6fb0"/>
        </linearGradient>
        <linearGradient id="photoGroup" x1="0" y1="0" x2="1" y2="1">
          <stop offset="0" stop-color="#d8c6a0"/>
          <stop offset=".5" stop-color="#b89a6a"/>
          <stop offset="1" stop-color="#4f6a9a"/>
        </linearGradient>
      </defs>

      <rect class="panel-bg" x="0" y="0" width="400" height="900" fill="url(#paperFold)"/>
      <rect class="panel-bg" x="400" y="0" width="400" height="900" fill="url(#paperFold)"/>
      <rect class="panel-bg" x="800" y="0" width="400" height="900" fill="url(#tealPanel)"/>

      <g role="img" aria-label="Photo: smiling volunteer tutor in a library with adult learners studying behind her">
        <path d="M0 0 H400 V420 C340 500 200 540 0 545 Z" fill="url(#photoWarm)"/>
      </g>
      <path class="swoosh-dark" d="M0 545 C200 540 340 500 400 420 V444 C340 524 200 568 0 572 Z" fill="var(--teal-dark)"/>
      <path class="swoosh-light" d="M0 572 C200 568 340 524 400 444 V476 C330 560 180 612 0 616 Z" fill="var(--teal)"/>
      <path class="foot-wave" d="M100 900 C200 884 320 876 400 876 V900 Z" fill="var(--teal)"/>

      <g role="img" aria-label="Photo: adults reading and writing together at a library table">
        <path d="M400 0 H800 V120 C640 150 520 260 400 430 Z" fill="url(#photoLibrary)"/>
      </g>
      <path class="swoosh-dark" d="M400 430 C520 260 640 150 800 120 V134 C650 162 530 270 400 450 Z" fill="var(--teal-dark)"/>
      <path class="swoosh-light" d="M400 450 C530 270 650 162 800 134 V210 C650 230 520 340 400 460 Z" fill="var(--teal)"/>

      <g role="img" aria-label="Photo: diverse group of adult students reading books together">
        <path d="M800 900 C880 780 1000 680 1200 640 V900 Z" fill="url(#photoGroup)"/>
      </g>
      <path class="swoosh-dark" d="M800 900 C880 780 1000 680 1200 640 V652 C1010 690 890 790 814 900 Z" fill="var(--teal-dark)"/>

      <circle cx="1002" cy="572" r="82" fill="var(--paper)"/>
    </svg>

    <!-- Panel 1: cover -->
    <h2 class="txt section-title" style="left:24px;top:390px;">VOLUNTEER</h2>
    <p class="txt body" style="left:24px;top:452px;">Enrich a Life!<br>Help an adult learn to read, write<br>or speak English</p>
    <div class="brand-name" style="left:40px;top:770px;width:320px;font-size:26px;">Reading Circle<br>Partners</div>

    <!-- Panel 2: tutors -->
    <h2 class="txt section-title" style="left:428px;top:452px;">TUTORS</h2>
    <ul class="txt body" style="left:428px;top:518px;list-style:none;line-height:23px;">
      <li>· No special skills or degrees needed —<br>&nbsp;&nbsp;just a degree of caring!</li>
      <li style="margin-top:23px;">· Training offered throughout the year</li>
      <li style="margin-top:23px;">· Tutors meet students weekly at a library</li>
      <li style="margin-top:23px;">· Instructional materials provided</li>
      <li style="margin-top:23px;">· Ongoing support available<br>&nbsp;Teach an adult to read and you’ll change<br>&nbsp;a life forever.</li>
    </ul>

    <!-- Panel 3: students -->
    <h2 class="txt section-title" style="left:826px;top:16px;">STUDENTS</h2>
    <div class="txt" style="left:826px;top:76px;">
      <p class="body">Students are adults in need of</p>
      <p class="list-italic">BASIC LITERACY SKILLS<br>PRE-GED SKILLS<br>CONVERSATIONAL ENGLISH</p>
      <p class="body">· Tutoring is free of charge<br>· Tutoring is one-on-one<br>· Flexible scheduling during library hours<br>· Lessons focus on student goals<br>&nbsp;If you can read, you can tutor!</p>
    </div>
    <p class="txt callout" style="left:825px;top:288px;">Don’t waste a moment!</p>
    <p class="txt small" style="left:827px;top:326px;">Contact us today to learn more.</p>
    <p class="txt small" style="left:827px;top:352px;">Volunteer Desk</p>
    <p class="txt phone" style="left:830px;top:370px;">555-014-2290</p>
    <p class="txt small" style="left:827px;top:404px;">Lakeview, Fernhill &amp; Southport</p>
    <p class="txt phone" style="left:827px;top:422px;">555-017-6831</p>
    <p class="txt phone email" style="left:827px;top:450px;">email: learn@readcircle.org</p>
    <div class="brand-name" style="left:922px;top:548px;width:160px;font-size:18px;">Reading Circle<br>Partners</div>
  </section>
</div>
</body>
</html>
```